Brightmill Data Works

Our company is about IT hardwares and IT solutions. IT hardware such as PC, RAMS, storage and servers. IT solutions such as project management, BA. We are also selling new technology too.

Target Market(s)

Consumer, Small to Medium Business, Corporate

Requirements
Must have
• The business card must have the following:
• Name:
• Title:
• Contact Number:
• Email address:
• Website:
• Color: Must match the logo color upgrade

```html
<!DOCTYPE html>
<html lang="en">
<head>
<meta charset="utf-8">
<title>Brightmill Data Works – Business Card</title>
<link rel="stylesheet" href="https://fonts.googleapis.com/css2?family=Kanit:wght@600&family=Lato:wght@400&display=swap">
<style>
  :root {
    --stage: #9a9a9a;
    --card-dark: #0f0f0f;
    --orange: #e3983a;
    --orange-deep: #c2652a;
    --orange-light: #cd7333;
    --white: #ffffff;
    --muted: #e6e6e6;
    --rule-dark: #8a8a8a;
  }
  * { margin: 0; padding: 0; box-sizing: border-box; }
  html, body {
    width: 1200px; height: 900px; overflow: hidden;
    background: var(--stage);
  }
  .canvas { position: relative; width: 1200px; height: 900px; }

  .card {
    position: absolute; width: 478px; height: 295px;
    box-shadow: 3px 5px 6px rgba(0,0,0,0.45);
    color: var(--white);
  }
  .card--back {
    left: 120px; top: 275px;
    background: var(--card-dark);
    border-radius: 0 46px 0 46px;
  }
  .card--front {
    left: 606px; top: 273px;
    background: radial-gradient(ellipse at 50% 40%, var(--orange-light), var(--orange-deep));
    border-radius: 46px 0 46px 0;
  }

  .brand-dot { position: absolute; border-radius: 50%; }
  .brand-name {
    position: absolute; font-family: "Kanit", sans-serif; font-weight: 600;
    color: var(--white); line-height: 1; text-transform: uppercase;
  }

  /* back card */
  .card--back .brand-dot { left: 330px; top: 51px; width: 40px; height: 40px; background: var(--orange); }
  .card--back .brand-main { right: 36px; top: 110px; font-size: 29px; letter-spacing: 0.5px; }
  .card--back .brand-sub { right: 36px; top: 142px; font-size: 13px; letter-spacing: 5px; }

  .holder { position: absolute; left: 29px; top: 159px; font-family: "Lato", sans-serif; }
  .holder-name { font-size: 17px; color: var(--orange); text-transform: uppercase; line-height: 1.2; }
  .holder-title { font-size: 13px; color: var(--muted); line-height: 1.2; }
  .holder-rule { position: absolute; left: 157px; top: 185px; width: 293px; height: 1px; background: var(--rule-dark); }

  .contacts {
    position: absolute; right: 30px; top: 207px; list-style: none;
    font-family: "Lato", sans-serif; font-size: 13px; color: var(--white); text-align: right;
  }
  .contacts li { display: flex; justify-content: flex-end; align-items: center; gap: 5px; height: 17.5px; }
  .contacts svg { width: 11px; height: 11px; fill: var(--orange); }

  /* front card */
  .card--front .brand-dot { left: 214px; top: 52px; width: 50px; height: 50px; background: var(--white); }
  .card--front .brand-main { left: 0; right: 0; top: 142px; text-align: center; font-size: 40px; letter-spacing: 0.5px; }
  .card--front .brand-sub { left: 0; right: 0; top: 188px; text-align: center; font-size: 19px; letter-spacing: 7px; }
  .front-rule { position: absolute; left: 98px; top: 226px; width: 281px; height: 1px; background: rgba(255,255,255,0.8); }
  .tagline {
    position: absolute; left: 0; right: 0; top: 240px; text-align: center;
    font-family: "Lato", sans-serif; font-size: 12.5px; letter-spacing: 1px; text-transform: uppercase;
  }
</style>
</head>
<body>
<main class="canvas">
  <section class="card card--back">
    <span class="brand-dot"></span>
    <div class="brand-name brand-main">Brightmill</div>
    <div class="brand-name brand-sub">Data Works</div>

    <div class="holder">
      <p class="holder-name">Daniel Harper</p>
      <p class="holder-title">Managing Director</p>
    </div>
    <span class="holder-rule"></span>

    <ul class="contacts">
      <li>044-555 210 387
        <svg viewBox="0 0 24 24"><path d="M3 9c0-3 4-5 9-5s9 2 9 5v2h-5V8.5c-1-.5-2.5-.7-4-.7s-3 .2-4 .7V11H3zM6 12h12l2 8H4z"/></svg>
      </li>
      <li>info@brightmill.com
        <svg viewBox="0 0 24 24"><path d="M2 5h20v14H2zM3.5 6.5 12 13l8.5-6.5z" fill-rule="evenodd"/></svg>
      </li>
      <li>www.brightmilldata.com
        <svg viewBox="0 0 24 24"><circle cx="12" cy="12" r="10"/><path d="M6 8c2 0 3 2 2 4s1 3 0 5M15 4c-1 2 1 3 3 3M16 14c2 0 3 1 2 4" stroke="#0f0f0f" stroke-width="1.6" fill="none"/></svg>
      </li>
    </ul>
  </section>

  <section class="card card--front">
    <span class="brand-dot"></span>
    <div class="brand-name brand-main">Brightmill</div>
    <div class="brand-name brand-sub">Data Works</div>
    <span class="front-rule"></span>
    <p class="tagline">IT Hardwares and IT Solutions</p>
  </section>
</main>
</body>
</html>
```